We’re a real estate firm that has landed a big builder in a neighboring state. Our branding needs...

We are a real estate firm who represents various builders along with doing resale here in Oregon. Our firm is growing to represent a big builder in Washington State and we’ll have another 40 brokers on our team. We need rebranding. As in, a new logo ( the house logo we have now looks cartoonish, hate it). We need new cards, something to really stand out. I’ve been thinking of using those NFC cards from ZEP or the ones with the seam color. I likely want two or three designs, a darker (as in a background color of black or grey) , a light one ( again I mean background color) and a credit card style (either plastic w an embossed name/number on front, or metal ). I’m thinking dark background for cc, or silver if it’s metal. That’s my thoughts, but you are the artists, so maybe you have an idea I haven’t considered. Our colors were black and red, but we don’t have to stick to that. Just nothing too busy. Oh, and we are typically representing the local, higher quality builders in our area (just below custom), but not national. Subdivisions are near the Kell Varney, Brisco, and Thornfield Crest sites. We are super excited, but without a lot of time to change the “look” of our brokerage. So I’ll be deciding and moving forward within 24 hours tops. Our name is Real Estate Summit Alliance ( we cant change the name because of timeline and business license) Thank you!

Industry/Entity Type

Real Estate

Contact Information for Business Card

The usual. Name of firm. Name of cardholder. Contact info.

Font styles to use
Serif
Sans Serif

Colors

Designer to choose colors to be used in the design.

Requirements
Must have
• A sleek or simple look. I included photos of cards with stylistic attributes we like. Thank you
Nice to have
• We really like the black backgrounds. With foil or embossed detail. We also like the black on black. Matte black card with raised shiny black detail. But still eye catching.
Should not have
• No ornate or busy looking style. We don’t want anything cluttered.

```html
<!DOCTYPE html>
<html lang="en">
<head>
<meta charset="utf-8">
<title>Real Estate Summit Alliance – Business Card</title>
<link href="https://fonts.googleapis.com/css2?family=Lato:wght@400;700&display=swap" rel="stylesheet">
<style>
  :root {
    --backdrop: #5b5b5d;
    --navy: #0d2a63;
    --ink: #1b1b1b;
    --paper: #ffffff;
    --rule: #9a9a9a;
  }
  * { margin: 0; padding: 0; box-sizing: border-box; }
  html, body { width: 1200px; height: 802px; overflow: hidden; }
  body { background: var(--backdrop); font-family: "Lato", sans-serif; position: relative; }

  .card {
    position: absolute;
    top: 274px;
    width: 443px;
    height: 265px;
    box-shadow: 2px 3px 6px rgba(0,0,0,.45);
  }
  .card--front { left: 136px; background: var(--paper); }
  .card--back { left: 624px; background: var(--navy); }

  .firm-name {
    position: absolute;
    display: flex;
    align-items: center;
    gap: 9px;
    font-weight: 700;
    line-height: 1.2;
  }
  .firm-name__dot { width: 10px; height: 10px; border-radius: 50%; flex: none; background: currentColor; }

  .card--front .firm-name { left: 26px; top: 132px; width: 185px; color: var(--navy); font-size: 18px; }

  .divider { position: absolute; left: 224px; top: 67px; width: 1px; height: 130px; background: var(--rule); }

  .contact { position: absolute; left: 242px; top: 64px; color: var(--ink); }
  .contact__name { color: var(--navy); font-weight: 700; font-size: 15px; letter-spacing: 0.2px; line-height: 1.1; }
  .contact__role { font-size: 12.5px; line-height: 1.1; }
  .contact__list { list-style: none; margin-top: 10px; }
  .contact__list li { font-size: 12.5px; line-height: 16px; display: flex; align-items: center; }
  .contact__list svg { width: 9px; height: 9px; margin-right: 4px; fill: var(--navy); flex: none; }
  .contact__address { font-size: 12.5px; line-height: 16px; margin-top: 6px; }

  .card--back .firm-name { left: 0; width: 100%; top: 112px; justify-content: center; color: var(--paper); font-size: 26px; }
</style>
</head>
<body>

  <section class="card card--front">
    <p class="firm-name"><span class="firm-name__dot"></span><span>Real Estate Summit Alliance</span></p>
    <div class="divider"></div>
    <div class="contact">
      <p class="contact__name">MARCUS DELANE</p>
      <p class="contact__role">Managing Director</p>
      <ul class="contact__list">
        <li><svg viewBox="0 0 10 10"><path d="M1 3c0-1 1-2 4-2s4 1 4 2v1H7V3H3v1H1zM2 5h6l1 4H1z"/></svg>044-555 210 384</li>
        <li><svg viewBox="0 0 10 10"><path d="M3 0h4a1 1 0 0 1 1 1v8a1 1 0 0 1-1 1H3a1 1 0 0 1-1-1V1a1 1 0 0 1 1-1zm0 1.5v6h4v-6z"/></svg>044-555 210 384</li>
        <li><svg viewBox="0 0 10 10"><path d="M0 2h10v6H0zm1 1v.3l4 2.5 4-2.5V3z"/></svg>info@summitalliance.com</li>
        <li><svg viewBox="0 0 10 10"><circle cx="5" cy="5" r="4.5"/></svg>www.summitalliance.com</li>
      </ul>
      <p class="contact__address">2410, Ridgeway Lane<br>Portland, OR 97205.</p>
    </div>
  </section>

  <section class="card card--back">
    <p class="firm-name"><span>Real Estate Summit Alliance</span></p>
  </section>

</body>
</html>
```